NZ First of it's kind solutions directory and marketplace for busy Mums needs a business card design

We need a business card design for our new nationwide business in NZ (long term plans to go global). We provide solutions to the everyday challenges that busy Mums face by connecting them with quality communities and suppliers of carefully selected, relevant products and services. We sell direct via our online marketplace. The final design should communicate our values of inclusivity, quality and smart solutions. Colours should incorporate our logo colour palette of #477077 and #6ba8b2. Our website is at https://www.brightnestmums.example

Target Market(s)

busy Mums, Age 28 – 50, female, income over $100K, location main centres NZ primarily but NZ wide. Is likely juggling work or career with a young family. Probably had hobbies which have fallen by the wayside.
-Wants to succeed in her chosen career without compromising on family life
-to successfully juggle her career without feeling like she is compromising her children
- Is time poor, something always has to give and it’s generally her health (she’ll stay up late, get stressed)
- probably ex corporate or professional career. Has discretional income

Industry/Entity Type

Business

Contact Information for Business Card

Lena Forbisher, Founder, BrightNestMums.example (Strapline Tap; Gather; Sorted), 47 Kowhai Terrace, Ellerslie, Auckland 1051, New Zealand. Mob: 021 483 517 Ph: +64 (0)9 571 4860

Font styles to use
Other font styles liked:
• Raleway, and/or Architects Daughter

Colors
00a990
33b8a4
86cfc6
cfeae6

Requirements
Must have
• the above details, streamline. the logo and colours associated with those logos
Should not have
• foil or metallic colours

```html
<!DOCTYPE html>
<html lang="en">
<head>
<meta charset="utf-8">
<title>BrightNestMums Business Card</title>
<link href="https://fonts.googleapis.com/css2?family=Raleway:wght@400;500;700;800&display=swap" rel="stylesheet">
<style>
  :root {
    --backdrop: #d9d9d7;
    --card: #ffffff;
    --teal: #00a990;
    --teal-soft: #33b8a4;
    --mint: #cfeae6;
    --slate: #477077;
    --slate-light: #6ba8b2;
    --muted: #3f9f90;
  }
  * { margin: 0; padding: 0; box-sizing: border-box; }
  html, body {
    width: 1200px; height: 1000px; overflow: hidden;
    background: var(--backdrop);
    font-family: "Raleway", sans-serif;
  }
  .canvas { position: relative; width: 1200px; height: 1000px; }

  .card {
    position: absolute;
    background: var(--card);
    box-shadow: 0 10px 24px rgba(0,0,0,0.25);
  }

  /* Front */
  .card-front { left: 169px; top: 112px; width: 592px; height: 338px; }
  .front-panel {
    position: absolute; left: 28px; top: 29px; width: 536px; height: 280px;
    background: var(--teal);
    display: flex; align-items: center; justify-content: center; gap: 16px;
  }
  .front-mark {
    width: 34px; height: 34px; border-radius: 50%;
    background: var(--mint);
  }
  .front-name {
    color: #ffffff; font-weight: 800; font-size: 40px; letter-spacing: -0.5px;
  }

  /* Back */
  .card-back { left: 390px; top: 558px; width: 601px; height: 342px; }
  .back-brand {
    position: absolute; left: 28px; top: 36px;
    display: flex; align-items: center; gap: 10px;
  }
  .back-mark {
    width: 26px; height: 26px; border-radius: 50%;
    background: var(--slate);
  }
  .back-name {
    color: var(--slate); font-weight: 800; font-size: 27px; letter-spacing: -0.3px;
  }
  .person {
    position: absolute; left: 0; right: 0; top: 100px;
    text-align: center; padding-left: 0;
    transform: translateX(-1px);
  }
  .person-name {
    color: var(--teal); font-size: 28px; font-weight: 500; line-height: 32px;
    margin-left: 0;
  }
  .person-role {
    color: var(--muted); font-size: 18px; font-weight: 400; line-height: 26px;
    margin-left: 28px;
  }
  .rule {
    position: absolute; left: 0; right: 0; top: 163px; height: 2px;
    background: var(--teal);
  }
  .address-band {
    position: absolute; left: 60px; top: 164px; width: 482px; height: 26px;
    background: var(--teal);
    border-radius: 0 0 14px 14px;
    color: #ffffff; font-size: 16px; font-weight: 500;
    display: flex; align-items: center; justify-content: center;
  }
  .contacts { position: absolute; left: 42px; top: 208px; list-style: none; }
  .contact {
    display: flex; align-items: center; height: 32px;
    color: var(--teal); font-size: 18px; font-weight: 500;
  }
  .contact svg { width: 22px; height: 22px; margin-right: 16px; flex: none; }
  .strapline { font-size: 13px; margin-left: 6px; }
</style>
</head>
<body>
<main class="canvas">
  <section class="card card-front" aria-label="Card front">
    <div class="front-panel">
      <span class="front-mark"></span>
      <span class="front-name">BrightNestMums</span>
    </div>
  </section>

  <section class="card card-back" aria-label="Card back">
    <div class="back-brand">
      <span class="back-mark"></span>
      <span class="back-name">BrightNestMums</span>
    </div>
    <div class="person">
      <p class="person-name">Lena Forbisher</p>
      <p class="person-role">Founder</p>
    </div>
    <div class="rule"></div>
    <div class="address-band">47 Kowhai Terrace, Ellerslie, Auckland 1051, New Zealand</div>
    <ul class="contacts">
      <li class="contact">
        <svg viewBox="0 0 24 24" aria-hidden="true"><path fill="#00a990" d="M3 8c0-2 2-3 9-3s9 1 9 3v2h-4V8.5c-1-.4-3-.6-5-.6s-4 .2-5 .6V10H3z"/><path fill="#00a990" d="M5 11l2-2h10l2 2v9H5z"/><circle cx="12" cy="15" r="2.6" fill="#fff"/></svg>
        <span>+64 (0)9 571 4860</span>
      </li>
      <li class="contact">
        <svg viewBox="0 0 24 24" aria-hidden="true"><path fill="#00a990" d="M6.6 3.5l3 3.2-1.8 2.2c1.2 2.6 3.1 4.5 5.6 5.8l2.2-1.8 3.2 3-1.6 3c-7.5-.6-12.8-6-13.4-13.5z"/></svg>
        <span>021 483 517</span>
      </li>
      <li class="contact">
        <svg viewBox="0 0 24 24" aria-hidden="true" fill="none" stroke="#00a990" stroke-width="2"><circle cx="12" cy="12" r="9"/><ellipse cx="12" cy="12" rx="4" ry="9"/><path d="M3 12h18M5 7h14M5 17h14"/></svg>
        <span>www.brightnestmums.example</span><span class="strapline">( Strapline Tap; Gather; Sorted )</span>
      </li>
    </ul>
  </section>
</main>
</body>
</html>
```